Tralha Cesto Website

Tralha Cesto is a brazilian Self Storage in a Box where customers can store all the clutter that they have out of their houses. We deliver one or more boxes at their homes, they fill the boxes with their stuff and we store it for them.

"Tralha" means something like "mess" in portuguese. So the name would means something like "Mess Box" or "Clutter Box".

How it works:
1) The customer asks for 1 or more boxes.
2) Tralha Cesto leaves the boxes at their houses
3) The clients fill the boxes with their stuff
4) Customers call Tralha Cesto for the pick up
5) We get the boxes and store them
6) When the customer wants the box back they can order it online or by phone and wait for the box delivery.
-

We have already produced a flyer to launch the service. You can see this flyer at "Project Files".

We want the website to have a startup "look and fell". Here are some websites of similar services that we like very much.
- www.crateowl.example
- www.stowpod.example

We are planning this launching website to have only 2 pages. The Landing Page and a FAQ page. We are producing an explainer video. The proposed designs must think about a special place to place the video.

We are still writing it´s content but you can use the flyer as a reference.

Thanks.
Updates

Project Deadline Extended
Reason: The project was refundable but as we have already received good design options, now we are turning it to Non Refundable and giving more time for new designers to send their proposals. Thanks.

Project Deadline Extended

Target Market(s)

Young couples having kids
Students
Families in need of more space at home

Industry/Entity Type

Store

Requirements
Must have
• Special place to place the explainer video (still being produced).

How it works drawing. You can use the one on the flyer or draw a new one (recomended).

Transparent box drawings (showing it´s content). I will serve to show the clients what they can store with the service.

Clutter Room Before/After Pic/drawings (showing how the service can benefit the client).

```html
<!DOCTYPE html>
<html lang="en">
<head>
<meta charset="utf-8">
<title>Tralha Cesto — Storage Made Simple</title>
<link href="https://fonts.googleapis.com/css2?family=Open+Sans:wght@400;600;700&family=Ubuntu:wght@500;700&display=swap" rel="stylesheet">
<style>
  :root {
    --bar-dark: #4a4a4a;
    --bar-text: #a9a9a9;
    --brand-blue: #1b73c2;
    --brand-orange: #f0a54c;
    --hero-peach: #f6c48a;
    --accent-orange: #f4b870;
    --pill-orange: #f7941d;
    --teal-heading: #24636f;
    --ink: #222;
    --body-text: #444;
    --soft-grey: #f4f4f4;
    --section-grey: #f2f2f2;
    --card-grey: #f6f6f6;
    --white: #fff;
    --dot-blue: #1a5f9e;
  }
  * { box-sizing: border-box; margin: 0; padding: 0; }
  html, body { width: 727px; height: 1200px; overflow: hidden; background: var(--white); }
  body { position: relative; font-family: "Open Sans", Arial, sans-serif; color: var(--ink); }
  .abs { position: absolute; }

  /* top bar */
  .top-bar { left: 0; top: 0; width: 727px; height: 19px; background: var(--bar-dark); font-size: 7.5px; color: var(--bar-text); }
  .top-links { left: 66px; top: 5px; display: flex; gap: 15px; }
  .top-phone { right: 66px; top: 5px; display: flex; align-items: center; gap: 5px; }

  /* header */
  .brand { left: 66px; top: 36px; display: flex; flex-direction: column; align-items: center; gap: 6px; }
  .brand-square { width: 30px; height: 30px; background: var(--brand-blue); border-radius: 4px; }
  .brand-name { font-family: "Ubuntu", sans-serif; font-weight: 700; font-size: 14px; color: var(--brand-blue); }
  .quote-cta { left: 539px; top: 32px; width: 121px; height: 32px; background: var(--brand-blue); border: 2px solid #4f9be0; text-align: center; color: var(--white); }
  .quote-cta strong { display: block; font-family: "Ubuntu", sans-serif; font-weight: 500; font-size: 10px; margin-top: 5px; }
  .quote-cta small { display: block; font-size: 4.5px; color: #9cc6ee; margin-top: 1px; }
  .quote-flag { left: 539px; top: 32px; width: 0; height: 0; border-top: 16px solid var(--brand-orange); border-right: 16px solid transparent; }
  .main-nav { top: 76px; left: 413px; display: flex; align-items: center; gap: 0; font-size: 8px; }
  .main-nav span { padding: 3px 6px; }
  .main-nav .nav-home { background: var(--pill-orange); color: var(--ink); border-radius: 2px; margin-right: 12px; }
  .main-nav .gap { margin-right: 12px; }

  /* hero */
  .hero { left: 0; top: 105px; width: 727px; height: 206px; background: var(--hero-peach); }
  .hero-edge { left: 0; top: 311px; width: 727px; height: 3px; background: #d8d8d8; }
  .video-frame { left: 66px; top: 124px; width: 235px; height: 166px; background: #f9dcb6; border-radius: 3px; padding: 8px; }
  .video-still { width: 219px; height: 150px; background: linear-gradient(160deg, #6f7a80, #4b5356 45%, #8a7256 80%, #3d3b38); position: relative; }
  .play-btn { left: 103px; top: 68px; width: 38px; height: 38px; border-radius: 50%; background: rgba(200,200,200,.6); }
  .new-ribbon { left: 224px; top: 134px; width: 84px; height: 12px; background: #d9201b; transform: rotate(34deg); color: var(--white); font-size: 7px; font-weight: 700; text-align: center; line-height: 12px; }
  .hero-title { left: 341px; top: 137px; font-family: "Ubuntu", sans-serif; font-weight: 500; font-size: 16px; color: var(--teal-heading); }
  .hero-copy { left: 342px; top: 168px; width: 320px; font-size: 6.6px; line-height: 13.4px; color: var(--ink); }
  .hero-points { left: 342px; top: 227px; font-size: 7.6px; font-weight: 600; line-height: 15px; color: #3a2a10; }
  .hero-cta { left: 575px; top: 258px; width: 85px; height: 24px; background: var(--white); border-radius: 2px; font-size: 7.6px; font-weight: 600; text-align: center; line-height: 24px; }
  .arrow { top: 197px; font-size: 18px; color: #555; }
  .slider-tab { left: 329px; top: 294px; width: 82px; height: 17px; background: var(--white); border-radius: 3px 3px 0 0; display: flex; justify-content: center; align-items: center; gap: 5px; }
  .slider-tab i { width: 7px; height: 7px; border-radius: 50%; background: var(--dot-blue); }
  .slider-tab i.active { background: #cfe2f3; }

  .section-title { width: 727px; left: 0; text-align: center; font-size: 11px; color: var(--ink); }
  .title-rule { width: 100px; left: 313px; height: 1px; background: #e4e4e4; }
  .title-rule::after { content: ""; position: absolute; left: 48px; top: -2px; width: 5px; height: 5px; border-radius: 50%; background: #e4e4e4; }

  /* feature cards */
  .feature-card { top: 409px; width: 188px; height: 160px; background: var(--card-grey); text-align: center; }
  .feature-icon { top: 367px; width: 80px; height: 80px; border-radius: 50%; border: 3px solid var(--accent-orange); background: var(--white); display: flex; align-items: center; justify-content: center; }
  .feature-card h3 { font-weight: 400; font-size: 11px; margin-top: 50px; letter-spacing: .2px; }
  .feature-card p { font-size: 6.5px; line-height: 13.3px; color: var(--body-text); margin: 12px 8px 0; }
  .learn-btn { display: inline-block; margin-top: 10px; width: 68px; height: 20px; line-height: 20px; background: var(--accent-orange); font-size: 7.6px; border-radius: 1px; }

  /* how it works */
  .how-band { left: 0; top: 593px; width: 727px; height: 250px; background: var(--section-grey); }
  .step-box { width: 224px; height: 76px; background: #f8f8f8; }
  .step-icon { width: 72px; height: 72px; border-radius: 50%; border: 3px solid var(--accent-orange); background: var(--white); display: flex; align-items: center; justify-content: center; }
  .step-text { width: 200px; }
  .step-text h4 { font-weight: 400; font-size: 8.4px; letter-spacing: .2px; }
  .step-text p { font-size: 6.5px; line-height: 13.3px; color: var(--body-text); margin-top: 6px; }

  /* clutter / get started */
  .col-heading { font-size: 11px; }
  .col-rule { height: 2px; background: var(--accent-orange); }
  .room-card { top: 896px; width: 137px; height: 117px; background: #f7f7f7; }
  .room-photo { width: 137px; height: 100px; }
  .room-card span { display: block; font-size: 7.6px; padding: 3px 5px; }
  .plan-card { top: 896px; width: 138px; height: 117px; background: #f3f3f3; }
  .plan-visual { left: 40px; top: 10px; width: 58px; height: 60px; border-radius: 2px; }
  .plan-price { left: 0; top: 77px; width: 138px; height: 40px; background: var(--accent-orange); text-align: center; font-size: 9.6px; line-height: 16px; padding-top: 4px; }

  .safety-strip { left: 66px; top: 1038px; width: 594px; height: 84px; background: #f3f3f3; }
  .safety-list { font-size: 6.7px; line-height: 18px; color: var(--ink); list-style: none; }
  .safety-list li::before { content: "✔"; font-size: 5px; margin-right: 9px; color: #555; }

  /* footer */
  .site-footer { left: 0; top: 1149px; width: 727px; height: 51px; background: var(--bar-dark); color: #e4e4e4; font-size: 6.8px; }
  .footer-links { left: 66px; top: 14px; }
  .footer-copy { left: 67px; top: 36px; }
  .social { top: 22px; width: 16px; height: 16px; border-radius: 50%; background: #d6dbe2; }
  .newsletter { left: 492px; top: 17px; width: 168px; height: 20px; background: var(--white); border: 1px solid #999; color: #888; font-size: 6.8px; line-height: 18px; padding-left: 7px; }
</style>
</head>
<body>

<div class="abs top-bar">
  <div class="abs top-links"><span>Blog</span><span>FAQ</span><span>We're Hiring</span></div>
  <div class="abs top-phone">
    <svg width="9" height="7" viewBox="0 0 9 7" aria-hidden="true"><rect x="0" y="2" width="9" height="5" rx="1" fill="#a9a9a9"/><rect x="1" y="0" width="7" height="2" rx="1" fill="#a9a9a9"/></svg>
    <span>1-800-555-0142</span>
  </div>
</div>

<header>
  <div class="abs brand">
    <div class="brand-square"></div>
    <div class="brand-name">Tralha Cesto</div>
  </div>
  <div class="abs quote-cta"><strong>GET FREE QUOTE</strong><small>Start your storage today</small></div>
  <div class="abs quote-flag"></div>
  <nav class="abs main-nav">
    <span class="nav-home">Home</span>
    <span class="gap">How it works</span>
    <span class="gap">Pricing</span>
    <span class="gap">Security</span>
    <span>Login</span>
  </nav>
</header>

<section>
  <div class="abs hero"></div>
  <div class="abs hero-edge"></div>
  <span class="abs arrow" style="left:10px">‹</span>
  <span class="abs arrow" style="left:708px">›</span>
  <div class="abs video-frame">
    <div class="video-still" role="img" aria-label="Explainer video still of a tidy home office">
      <div class="abs play-btn"></div>
      <svg class="abs" style="left:117px;top:79px" width="12" height="16" viewBox="0 0 12 16" aria-hidden="true"><path d="M1 1 L11 8 L1 15 Z" fill="#666"/></svg>
    </div>
  </div>
  <div class="abs new-ribbon">NEW</div>
  <h1 class="abs hero-title">Storage Made Simple!</h1>
  <p class="abs hero-copy">During a trip to Amsterdam last year, I was pleasantly surprised to see more bicycles on the road than cars. Most riders were dressed in suits and ties or skirts and stockings, their dress shoes pushing the pedals as they moved sedately along wide, clearly marked paths that paralleled the motorized traffic</p>
  <div class="abs hero-points">- Fully Customizable<br>- Easy to modify &amp; Change colors</div>
  <div class="abs hero-cta">GET FREE QUOTE</div>
  <div class="abs slider-tab"><i></i><i></i><i class="active"></i><i></i><i></i></div>
</section>

<section>
  <h2 class="abs section-title" style="top:333px;font-weight:400">What is Tralha Cesto?</h2>
  <div class="abs title-rule" style="top:355px"></div>

  <div class="abs feature-card" style="left:66px"><h3>WHAT YOU STORE</h3><p>Lid est laborum dolo rumes fugats untras. Etharums ser quidem rerum facilis dolores nemis omnis fugats vitaes nemo minima rerums unsers sadips amets.</p><span class="learn-btn">Learn More</span></div>
  <div class="abs feature-card" style="left:268px"><h3>CONVENIENT PICK UP</h3><p>Lid est laborum dolo rumes fugats untras. Etharums ser quidem rerum facilis dolores nemis omnis fugats vitaes nemo minima rerums unsers sadips amets.</p><span class="learn-btn">Learn More</span></div>
  <div class="abs feature-card" style="left:472px"><h3>RETURN OF STORED ITEMS</h3><p>Lid est laborum dolo rumes fugats untras. Etharums ser quidem rerum facilis dolores nemis omnis fugats vitaes nemo minima rerums unsers sadips amets.</p><span class="learn-btn">Learn More</span></div>

  <div class="abs feature-icon" style="left:118px">
    <svg width="34" height="30" viewBox="0 0 34 30" aria-hidden="true"><rect x="1" y="12" width="32" height="17" rx="4" fill="#111"/><path d="M17 0 V14 M11 8 L17 14 L23 8" stroke="#111" stroke-width="3" fill="none"/><path d="M10 12 h14" stroke="#fff" stroke-width="2"/></svg>
  </div>
  <div class="abs feature-icon" style="left:320px">
    <svg width="48" height="38" viewBox="0 0 48 38" aria-hidden="true"><rect x="2" y="12" width="10" height="18" fill="#111"/><rect x="4" y="6" width="6" height="6" fill="#111"/><rect x="14" y="14" width="20" height="16" fill="#111"/><path d="M34 2 V30 M34 30 H46" stroke="#111" stroke-width="3" fill="none"/><path d="M18 14 L22 3 H33" stroke="#111" stroke-width="3" fill="none"/><circle cx="18" cy="32" r="5" fill="#111"/><circle cx="30" cy="32" r="5" fill="#111"/></svg>
  </div>
  <div class="abs feature-icon" style="left:524px">
    <svg width="50" height="34" viewBox="0 0 50 34" aria-hidden="true" fill="none" stroke="#111" stroke-width="2"><circle cx="11" cy="11" r="9"/><path d="M11 5 V11 L15 13"/><path d="M20 8 H34 V26 H8 V20"/><path d="M34 14 H42 L48 21 V26 H34"/><circle cx="14" cy="28" r="4" fill="#fff"/><circle cx="40" cy="28" r="4" fill="#fff"/></svg>
  </div>
</section>

<section>
  <div class="abs how-band"></div>
  <h2 class="abs section-title" style="top:606px;font-weight:400">How it Works</h2>
  <div class="abs title-rule" style="top:628px"></div>

  <div class="abs step-box" style="left:130px;top:651px"></div>
  <div class="abs step-box" style="left:436px;top:651px"></div>
  <div class="abs step-box" style="left:130px;top:742px"></div>
  <div class="abs step-box" style="left:436px;top:742px"></div>

  <div class="abs step-icon" style="left:65px;top:652px">
    <svg width="44" height="40" viewBox="0 0 44 40" aria-hidden="true"><path d="M6 4 L14 34 H22" stroke="#111" stroke-width="3" fill="none"/><rect x="16" y="14" width="14" height="12" fill="#111" transform="rotate(-18 23 20)"/><rect x="26" y="10" width="12" height="12" fill="#111" transform="rotate(-18 32 16)"/><circle cx="16" cy="35" r="4" fill="#111"/></svg>
  </div>
  <div class="abs step-text" style="left:155px;top:661px"><h4>PICK THE SIZE THAT MEETS</h4><p>Meet Norvale, pixel perfect responsive template, excellent choice for professional business websites. Attract your visitors with clean and powerful look.</p></div>

  <div class="abs step-icon" style="left:372px;top:652px">
    <svg width="34" height="40" viewBox="0 0 34 40" aria-hidden="true"><rect x="1" y="1" width="32" height="38" rx="5" fill="#111"/><circle cx="17" cy="23" r="9" fill="none" stroke="#fff" stroke-width="2.5"/><circle cx="26" cy="7" r="2" fill="#fff"/></svg>
  </div>
  <div class="abs step-text" style="left:462px;top:661px"><h4>PICK UP OF YOUR ITEMS</h4><p>Meet Norvale, pixel perfect responsive template, excellent choice for professional business websites. Attract your visitors with clean and powerful look.</p></div>

  <div class="abs step-icon" style="left:65px;top:743px">
    <svg width="46" height="26" viewBox="0 0 46 26" aria-hidden="true"><rect x="0" y="2" width="30" height="17" fill="#111"/><path d="M30 8 H38 L45 15 V19 H30 Z" fill="#111"/><circle cx="9" cy="21" r="4" fill="#111" stroke="#fff" stroke-width="1.5"/><circle cx="37" cy="21" r="4" fill="#111" stroke="#fff" stroke-width="1.5"/></svg>
  </div>
  <div class="abs step-text" style="left:155px;top:752px"><h4>PACK THE VAN</h4><p>Meet Norvale, pixel perfect responsive template, excellent choice for professional business websites. Attract your visitors with clean and powerful look.</p></div>

  <div class="abs step-icon" style="left:372px;top:743px">
    <svg width="34" height="44" viewBox="0 0 34 44" aria-hidden="true" fill="none" stroke="#111" stroke-width="2.5"><rect x="4" y="8" width="20" height="34" rx="3"/><rect x="9" y="18" width="10" height="12" fill="#111"/><path d="M26 2 a8 8 0 0 1 6 8 M25 6 a4 4 0 0 1 3 4"/></svg>
  </div>
  <div class="abs step-text" style="left:462px;top:752px"><h4>SECURELY STORE</h4><p>Meet Norvale, pixel perfect responsive template, excellent choice for professional business websites. Attract your visitors with clean and powerful look.</p></div>
</section>

<section>
  <h2 class="abs col-heading" style="left:66px;top:862px;font-weight:400">Clutter Room</h2>
  <div class="abs col-rule" style="left:66px;top:882px;width:288px"></div>
  <div class="abs room-card" style="left:67px">
    <div class="room-photo" role="img" aria-label="Cluttered room before storage" style="background:linear-gradient(150deg,#8a95a0,#5a5f63 50%,#6d5a48)"></div>
    <span>Clutter Room Before</span>
  </div>
  <div class="abs room-card" style="left:217px">
    <div class="room-photo" role="img" aria-label="Tidy room after storage" style="background:linear-gradient(150deg,#6e7c84,#4b5458 50%,#8a7256)"></div>
    <span>Clutter Room After</span>
  </div>

  <h2 class="abs col-heading" style="left:374px;top:862px;font-weight:400">GET STARTED</h2>
  <div class="abs col-rule" style="left:374px;top:882px;width:287px"></div>
  <div class="abs plan-card" style="left:374px">
    <div class="abs plan-visual" role="img" aria-label="Tall storage crate on pallet" style="background:linear-gradient(#9a9a9a,#5e5e5e)"></div>
    <div class="abs plan-price">a partir de<br>$ 00.00/mes</div>
  </div>
  <div class="abs plan-card" style="left:522px">
    <div class="abs plan-visual" role="img" aria-label="Wide lidded storage bin" style="left:32px;width:74px;height:50px;top:16px;background:linear-gradient(#555,#2b2b2b)"></div>
    <div class="abs plan-price">a partir de<br>$ 00.00/mes</div>
  </div>

  <div class="abs safety-strip">
    <svg class="abs" style="left:16px;top:13px" width="50" height="58" viewBox="0 0 50 58" aria-hidden="true" fill="none" stroke="#111" stroke-width="3"><ellipse cx="24" cy="8" rx="20" ry="6"/><path d="M4 8 V48 a20 6 0 0 0 24 5"/><path d="M44 8 V30"/><circle cx="38" cy="44" r="11" fill="#fff"/><rect x="33" y="43" width="10" height="8" fill="#111" stroke="none"/><path d="M35 43 V40 a3 3 0 0 1 6 0 V43" stroke-width="2"/></svg>
    <ul class="abs safety-list" style="left:84px;top:14px">
      <li>Apartment fires that can arise from careless neighbors</li>
      <li>Theft with our secure storage and 24/hr surveillance</li>
      <li>Natural disasters such as earthquakes</li>
    </ul>
    <ul class="abs safety-list" style="left:337px;top:14px">
      <li>Apartment fires that can arise from careless neighbors</li>
      <li>Theft with our secure storage and 24/hr surveillance</li>
      <li>Natural disasters such as earthquakes</li>
    </ul>
  </div>
</section>

<footer class="abs site-footer">
  <div class="abs footer-links">How it works &nbsp;&nbsp;| Pricing| &nbsp;News &nbsp;| &nbsp;About &nbsp;| &nbsp;Contact</div>
  <div class="abs footer-copy">© 2014 &nbsp;Tralha Cesto, All Rights Reserved</div>
  <div class="abs social" style="left:338px"></div>
  <div class="abs social" style="left:358px"></div>
  <div class="abs social" style="left:378px"></div>
  <div class="abs newsletter">Sign up to our newsletter</div>
</footer>

</body>
</html>
```